Keystone Trench Co Business Card*

Looking for a professional, clean and crisp business card

I am in the underground utilities industry and am just looking for a really impressive business card. I would like our card to be white with our symbol crisp and clear with it protruding. I also have a business partner that will require his name and info on the card once the design is set. I would like to have our website info on the card which is;
http://keystonetrenchco.example/

Contact Information for Business Card

Website, contact name, number and email

```html
<!DOCTYPE html>
<html lang="en">
<head>
<meta charset="utf-8">
<title>Keystone Trench Co – Business Card</title>
<link href="https://fonts.googleapis.com/css2?family=Roboto:wght@400;500;700&display=swap" rel="stylesheet">
<style>
  :root {
    --backdrop: #4a70b8;
    --card: #ffffff;
    --accent: #6597dc;
    --ink-dark: #1f1f1f;
    --ink-name: #4b4f55;
    --ink-body: #666a70;
    --rule: #8a8d92;
    --ghost: #f3f3f3;
  }
  * { margin: 0; padding: 0; box-sizing: border-box; }
  html, body {
    width: 1200px; height: 766px; overflow: hidden;
    background: var(--backdrop);
    font-family: "Roboto", Arial, sans-serif;
  }
  .card {
    position: absolute; top: 253px;
    width: 466px; height: 274px;
    background: var(--card);
    border-radius: 22px;
    overflow: hidden;
    box-shadow: 0 10px 40px rgba(20, 40, 90, 0.35);
  }
  .card--front { left: 112px; }
  .card--back { left: 620px; }

  .accent-bar {
    position: absolute; left: 105px; width: 250px; height: 4px;
    background: var(--accent); border-radius: 2px;
  }
  .accent-bar--top { top: 0; }
  .accent-bar--bottom { bottom: 0; left: 107px; }

  .brand {
    position: absolute; display: flex; align-items: center;
    color: var(--ink-dark); font-weight: 700; line-height: 1.05;
    text-transform: uppercase;
  }
  .brand__dot { border-radius: 50%; background: var(--accent); flex: none; }

  .brand--front { left: 128px; top: 106px; font-size: 26px; gap: 12px; }
  .brand--front .brand__dot { width: 40px; height: 40px; }

  .brand--small { left: 62px; top: 127px; font-size: 12px; gap: 6px; }
  .brand--small .brand__dot { width: 16px; height: 16px; }

  .ghost-mark {
    position: absolute; left: -60px; top: 8px;
    width: 250px; height: 250px; border-radius: 50%;
    border: 14px solid var(--ghost);
  }

  .divider {
    position: absolute; left: 202px; top: 81px;
    width: 2px; height: 125px; background: var(--rule);
  }

  .person { position: absolute; left: 223px; top: 65px; }
  .person__name {
    font-size: 17.5px; font-weight: 700; color: var(--ink-name);
    letter-spacing: -0.2px;
  }
  .person__role { font-size: 11px; color: var(--ink-body); margin-top: 1px; }

  .contacts { position: absolute; left: 222px; top: 126px; list-style: none; }
  .contacts li {
    display: flex; align-items: flex-start; gap: 7px;
    font-size: 11.5px; color: var(--ink-body); line-height: 14px;
    margin-bottom: 8.5px;
  }
  .contacts svg { width: 11px; height: 13px; flex: none; fill: var(--accent); }
</style>
</head>
<body>

<section class="card card--front">
  <span class="accent-bar accent-bar--top"></span>
  <div class="brand brand--front">
    <span class="brand__dot"></span>
    <span>Keystone<br>Trench Co</span>
  </div>
  <span class="accent-bar accent-bar--bottom"></span>
</section>

<section class="card card--back">
  <span class="ghost-mark"></span>
  <div class="brand brand--small">
    <span class="brand__dot"></span>
    <span>Keystone<br>Trench Co</span>
  </div>

  <span class="divider"></span>

  <div class="person">
    <h1 class="person__name">DALE MARCHETTI</h1>
    <p class="person__role">Owner</p>
  </div>

  <ul class="contacts">
    <li>
      <svg viewBox="0 0 24 24"><path d="M6.6 10.8a15.1 15.1 0 0 0 6.6 6.6l2.2-2.2c.3-.3.7-.4 1-.2 1.1.4 2.3.6 3.6.6.6 0 1 .4 1 1V20c0 .6-.4 1-1 1A17 17 0 0 1 3 4c0-.6.4-1 1-1h3.5c.6 0 1 .4 1 1 0 1.3.2 2.5.6 3.6.1.3 0 .7-.2 1z"/></svg>
      <span>778-555-0142</span>
    </li>
    <li>
      <svg viewBox="0 0 24 24"><path d="M2 5h20v14H2z M3.5 6.5 12 13l8.5-6.5" stroke="#fff" stroke-width="1.5"/></svg>
      <span>Dale@keystonetrenchco.example</span>
    </li>
    <li>
      <svg viewBox="0 0 24 24"><circle cx="12" cy="12" r="10"/><path d="M2 12h20M12 2c3 3 3 17 0 20M12 2c-3 3-3 17 0 20" stroke="#fff" stroke-width="1.4" fill="none"/></svg>
      <span>keystonetrenchco.example</span>
    </li>
    <li>
      <svg viewBox="0 0 24 24"><path d="M12 1a8 8 0 0 0-8 8c0 6 8 14 8 14s8-8 8-14a8 8 0 0 0-8-8zm0 11a3 3 0 1 1 0-6 3 3 0 0 1 0 6z"/></svg>
      <span>Cedar Hollow, British Columbia,<br>Canada</span>
    </li>
  </ul>
</section>

</body>
</html>
```